Web Design Project and logo

We need a new web design and logo for www.kz7ventures.com

It is a mobile app development company. Site needs to look very cool/trendy as does the new logo.

Looking for the design (uncoded) and the logo file that my developers can then use to build out the site.

An example of a nice competitor site is www.thecodegarage.com

We want something that looks fresh, clean and hip.

Also development of business cards.

Target Market(s)

Small to mid sized companies

Industry/Entity Type

Business

Requirements
Must have
• Ability to request a quote
Should look very trendy like www.thecodegarage.com as an example of a competitor site

```html
<!DOCTYPE html>
<html lang="en">
<head>
<meta charset="utf-8">
<title>kz7 ventures — Mobile App Development</title>
<link rel="stylesheet" href="https://fonts.googleapis.com/css2?family=Arimo:wght@400;700&display=swap">
<style>
  :root {
    --brand-blue: #009fdb;
    --ink: #444448;
    --ink-soft: #77777a;
    --panel: #f4f4f4;
    --rule: #dcdcdc;
    --dark-btn: #2a2a2a;
    --white: #ffffff;
    --logo-red: #d9363e;
  }
  * { box-sizing: border-box; margin: 0; padding: 0; }
  html, body { width: 1200px; height: 1000px; overflow: hidden; }
  body {
    position: relative;
    background: var(--white);
    font-family: "Arimo", Arial, sans-serif;
    color: var(--ink);
  }
  .abs { position: absolute; }

  /* Header */
  .site-header { position: absolute; left: 0; top: 0; width: 1200px; height: 146px; background: var(--white); }
  .brand { position: absolute; left: 48px; top: 52px; display: flex; align-items: center; gap: 16px; }
  .brand-mark { width: 38px; height: 38px; background: var(--logo-red); }
  .brand-name { font-size: 36px; font-weight: 700; color: var(--logo-red); letter-spacing: 0.5px; }

  .search { position: absolute; left: 795px; top: 82px; width: 190px; height: 30px;
    border: 1px solid #b0b0b0; border-radius: 6px; background: var(--white);
    font-size: 18px; color: var(--ink-soft); padding: 4px 0 0 9px; }
  .search svg { position: absolute; right: 10px; top: 5px; }

  .social { position: absolute; top: 78px; width: 32px; height: 32px; border-radius: 5px; background: #9aa3ad; }

  /* Navigation */
  .main-nav { position: absolute; left: 0; top: 146px; width: 1200px; height: 40px; background: var(--brand-blue); }
  .main-nav a { position: absolute; top: 13px; font-size: 17px; color: var(--white); text-decoration: none; }

  /* Hero */
  .hero { position: absolute; left: 0; top: 186px; width: 1200px; height: 362px; background: var(--panel);
    border-bottom: 3px solid var(--rule); }
  .hero-title { position: absolute; left: 46px; top: 44px; font-size: 37px; font-weight: 400; color: var(--ink-soft); letter-spacing: 0.3px; }
  .hero-text { position: absolute; left: 51px; top: 101px; width: 440px; font-size: 20px; line-height: 25px; color: var(--ink); }
  .btn { position: absolute; top: 262px; height: 48px; border-radius: 12px; color: var(--white);
    font-size: 22px; line-height: 48px; text-align: center; text-decoration: none; }
  .btn-dark { left: 55px; width: 250px; background: var(--dark-btn); }
  .btn-blue { left: 332px; width: 249px; background: var(--brand-blue); }
  .hero-devices { position: absolute; left: 650px; top: 36px; width: 510px; height: 314px;
    background: linear-gradient(180deg, #3a3d44 0%, #1e2026 55%, #cfd1d4 100%); border-radius: 8px; }

  /* Services */
  .service { position: absolute; width: 440px; }
  .service-icon { position: absolute; width: 54px; height: 47px; border-radius: 9px; background: var(--brand-blue); }
  .service-icon svg { display: block; margin: 8px auto 0; }
  .service-title { position: absolute; font-size: 21px; font-weight: 700; color: var(--ink); letter-spacing: 0.3px; }
  .service-text { position: absolute; width: 430px; font-size: 20px; line-height: 26px; color: var(--ink); }

  /* Footer */
  .site-footer { position: absolute; left: 0; top: 912px; width: 1200px; height: 88px; background: var(--panel);
    border-top: 3px solid var(--rule); }
  .site-footer a { position: absolute; top: 30px; font-size: 18px; color: var(--ink); text-decoration: none; letter-spacing: -0.3px; }
</style>
</head>
<body>

<header class="site-header">
  <div class="brand">
    <span class="brand-mark"></span>
    <span class="brand-name">kz7 ventures</span>
  </div>
  <div class="search">Search
    <svg width="20" height="20" viewBox="0 0 20 20"><circle cx="8" cy="8" r="6" fill="none" stroke="#555" stroke-width="1.6"/><line x1="12.5" y1="12.5" x2="18" y2="18" stroke="#555" stroke-width="2"/></svg>
  </div>
  <span class="social" style="left:1050px" role="img" aria-label="Social network link"></span>
  <span class="social" style="left:1098px" role="img" aria-label="Social network link"></span>
  <span class="social" style="left:1146px" role="img" aria-label="News feed link"></span>
</header>

<nav class="main-nav">
  <a style="left:47px">HOME</a>
  <a style="left:142px">OUR SERVICES</a>
  <a style="left:332px">A BOUT</a>
  <a style="left:458px">LATEST NEWS</a>
  <a style="left:634px">CONTACT US</a>
</nav>

<section class="hero">
  <h1 class="hero-title">THE NO.1 APP PROVIDER</h1>
  <p class="hero-text">Lorem ipsum dolor sit amet, con sectetuer adipiscing elit. Aenean commodo ligula eget dolor. Aenean massa. Cum sociis natoque</p>
  <a class="btn btn-dark">FIND OUT MORE</a>
  <a class="btn btn-blue">CONTACT US TODAY</a>
  <div class="hero-devices" role="img" aria-label="Product photo of tablets and smartphones showing app screens"></div>
</section>

<section class="services">
  <div class="service-icon abs" style="left:78px;top:592px">
    <svg width="22" height="32" viewBox="0 0 22 32"><rect x="2" y="1" width="18" height="30" rx="3" fill="none" stroke="#fff" stroke-width="2.5"/><circle cx="11" cy="26" r="1.6" fill="#fff"/></svg>
  </div>
  <h2 class="service-title" style="left:145px;top:604px">MOBILE SERVICES</h2>
  <p class="service-text" style="left:143px;top:637px">Lorem ipsum dolor sit amet, consectetuer ad elit. Aenean commodo ligula eget dolor. Aen</p>

  <div class="service-icon abs" style="left:637px;top:590px">
    <svg width="32" height="32" viewBox="0 0 32 32"><g stroke="#fff" stroke-width="5"><line x1="16" y1="2" x2="16" y2="30"/><line x1="2" y1="16" x2="30" y2="16"/><line x1="6" y1="6" x2="26" y2="26"/><line x1="26" y1="6" x2="6" y2="26"/></g><circle cx="16" cy="16" r="10" fill="#fff"/><circle cx="16" cy="16" r="4.5" fill="#009fdb"/></svg>
  </div>
  <h2 class="service-title" style="left:703px;top:605px">DEVELOPMENT</h2>
  <p class="service-text" style="left:701px;top:637px">Lorem ipsum dolor sit amet, consectetuer ad elit. Aenean commodo ligula eget dolor. Aen</p>

  <div class="service-icon abs" style="left:82px;top:746px">
    <svg width="26" height="32" viewBox="0 0 26 32"><circle cx="13" cy="9" r="6" fill="none" stroke="#fff" stroke-width="2.5"/><path d="M2 30 Q2 17 13 17 Q24 17 24 30 Z" fill="none" stroke="#fff" stroke-width="2.5"/></svg>
  </div>
  <h2 class="service-title" style="left:147px;top:764px">SUPPORT</h2>
  <p class="service-text" style="left:145px;top:793px">Lorem ipsum dolor sit amet, consectetuer ad elit. Aenean commodo ligula eget dolor. Aen</p>

  <div class="service-icon abs" style="left:637px;top:740px">
    <svg width="36" height="32" viewBox="0 0 36 32"><rect x="3" y="3" width="30" height="20" fill="none" stroke="#fff" stroke-width="3"/><rect x="14" y="23" width="8" height="5" fill="#fff"/><rect x="9" y="27" width="18" height="3" fill="#fff"/></svg>
  </div>
  <h2 class="service-title" style="left:702px;top:760px">DESIGN</h2>
  <p class="service-text" style="left:703px;top:791px">Lorem ipsum dolor sit amet, consectetuer ad elit. Aenean commodo ligula eget dolor. Aen</p>
</section>

<footer class="site-footer">
  <a style="left:82px">HOME</a>
  <a style="left:163px">OUR SERVICES</a>
  <a style="left:320px">A BOUT</a>
  <a style="left:410px">LATEST NEWS</a>
  <a style="left:552px">CONTACT US</a>
</footer>

</body>
</html>
```